Tech business card design

We need an amazing business card design for our new business 'Pexla' a marketing tech startup based in Sydney, Australia. We provide an online marketplace for businesses to search and buy advertising media, connect with service providers and learn more about marketing. We wish to communicate 'cool tech', reliability and professionalism and design based around our logo.

Target Market(s)

Business Owners

Contact Information for Business Card

Name
Position
Email Address
Website
Phone Number

Font styles to use
Other font styles liked:
• Avenir & Avenir Next

Colors

Designer to choose colors to be used in the design.

```html
<!DOCTYPE html>
<html lang="en">
<head>
<meta charset="UTF-8">
<title>Pexla Business Card</title>
<link href="https://fonts.googleapis.com/css2?family=Mulish:ital,wght@0,400;0,600;0,800;0,900;1,700&display=swap" rel="stylesheet">
<style>
  :root {
    --page-bg: #e6e7ec;
    --navy: #1b1d4e;
    --navy-texture: #222558;
    --white: #ffffff;
    --rule: #c9cbe0;
    --text-soft: #e9eaf4;
  }
  * { box-sizing: border-box; margin: 0; padding: 0; }
  html, body {
    width: 1200px; height: 800px; overflow: hidden;
    background: var(--page-bg);
    font-family: "Mulish", "Avenir Next", sans-serif;
  }
  .canvas {
    position: relative; width: 1200px; height: 800px;
    display: flex; justify-content: center; align-items: center; gap: 100px;
  }
  .card {
    position: relative; width: 360px; height: 620px;
    background: var(--navy); overflow: hidden;
    box-shadow: 0 18px 40px rgba(20, 22, 50, 0.25);
    color: var(--white);
  }

  /* Front */
  .front-texture {
    position: absolute; top: 0; left: 0; right: 0; height: 400px;
    background: linear-gradient(200deg, var(--navy-texture) 0%, var(--navy-texture) 45%, var(--navy) 100%);
  }
  .front-name {
    position: absolute; left: 36px; bottom: 70px;
    font-weight: 900; font-size: 92px; letter-spacing: -2px; color: var(--white);
  }

  /* Back */
  .back-content {
    position: absolute; top: 0; left: 0; right: 0; bottom: 80px;
    display: flex; flex-direction: column; align-items: center; text-align: center;
  }
  .back-name {
    margin-top: 44px; font-weight: 900; font-size: 84px; letter-spacing: -2px;
  }
  .person { margin-top: 14px; font-weight: 800; font-size: 22px; }
  .role { font-size: 15px; font-weight: 400; color: var(--text-soft); margin-top: 2px; }
  .rule { width: 210px; height: 1px; background: var(--rule); margin: 14px 0; }
  .rule-last { margin-bottom: 10px; }
  .label { font-style: italic; font-weight: 700; font-size: 13px; }
  .value { font-size: 15px; color: var(--text-soft); margin-bottom: 6px; }
  .address { font-size: 15px; line-height: 1.35; color: var(--text-soft); }
  .social { display: flex; gap: 10px; }
  .social span {
    width: 26px; height: 26px; border-radius: 50%;
    border: 2px solid var(--white); display: block;
  }
  .footer-band { position: absolute; left: 0; right: 0; bottom: 0; height: 90px; }
  .website {
    position: absolute; left: 0; right: 0; bottom: 18px; text-align: center;
    color: var(--navy); font-size: 17px; font-weight: 600; letter-spacing: 0.3px;
  }
  .website b { font-weight: 900; }
</style>
</head>
<body>
<main class="canvas">
  <section class="card card-front">
    <div class="front-texture" role="img" aria-label="Faint decorative brand texture in deep navy"></div>
    <div class="front-name">pexla</div>
  </section>

  <section class="card card-back">
    <div class="back-content">
      <div class="back-name">pexla</div>
      <div class="person">Mara Quill</div>
      <div class="role">Manager</div>
      <div class="rule"></div>
      <div class="label">Phone:</div>
      <div class="value">555.555.5555</div>
      <div class="label">Email:</div>
      <div class="value">hello@pexlamail.com</div>
      <div class="rule"></div>
      <div class="address">PO BOX 123, your address<br>2nd street Sydney<br>Australia</div>
      <div class="rule rule-last"></div>
      <div class="social" aria-label="Social links"><span></span><span></span></div>
    </div>
    <svg class="footer-band" viewBox="0 0 360 90" preserveAspectRatio="none" aria-hidden="true">
      <path d="M0 20 H40 Q52 20 52 32 V40 Q52 50 62 50 H298 Q308 50 308 40 V32 Q308 20 320 20 H360 V90 H0 Z" fill="#ffffff"/>
    </svg>
    <div class="website">www.<b>pexlaweb</b>.com</div>
  </section>
</main>
</body>
</html>
```